Brightfield Ventures Inc. Letterhead

Creation of attractive and eye catching letterhead for a business start-up for the construction industry. Letterhead must relate to construction, but avoid standard hammer and tools in the design.

I forgot to add some details, sorry about that. Some pertinent info: Ph: 916-555-0187 brightfieldventures.example 448 Willowmere Ave, Ste 210 Folsom, CA 95999 info@brightfieldventures.example not sure if slogan should be in there" “Bringing building teams together to shape a stronger, steadier trade.” must be able to be used in word. Thanks!

```html
<!DOCTYPE html>
<html lang="en">
<head>
<meta charset="utf-8">
<title>Brightfield Ventures Inc. Letterhead</title>
<link href="https://fonts.googleapis.com/css2?family=Lato:wght@400;700;900&display=swap" rel="stylesheet">
<style>
  :root {
    --backdrop: #d9d9d9;
    --paper: #f0f0f0;
    --navy: #1f2a5c;
    --red: #c0272d;
    --ink: #555555;
  }
  * { margin: 0; padding: 0; box-sizing: border-box; }
  html, body {
    width: 1200px;
    height: 1154px;
    overflow: hidden;
    background: var(--backdrop);
    font-family: "Lato", Arial, sans-serif;
  }
  .letterhead {
    position: absolute;
    left: 314px;
    top: 149px;
    width: 622px;
    height: 875px;
    background: var(--paper);
  }
  .brand {
    position: absolute;
    left: 48px;
    top: 84px;
    display: flex;
    align-items: center;
    gap: 10px;
  }
  .brand-mark {
    width: 14px;
    height: 14px;
    background: var(--red);
  }
  .brand-name {
    font-weight: 900;
    font-size: 17px;
    letter-spacing: 1.2px;
    color: var(--navy);
    text-transform: uppercase;
    line-height: 1.15;
  }
  .contact {
    position: absolute;
    left: 422px;
    top: 86px;
    font-size: 10.5px;
    font-style: normal;
    color: var(--ink);
    line-height: 14px;
  }
  .contact .address { margin-bottom: 7px; }
  .contact-row {
    display: flex;
    align-items: center;
    gap: 6px;
    line-height: 14.5px;
  }
  .contact-row svg { width: 10px; height: 10px; flex: none; }
  .footer {
    position: absolute;
    left: 0;
    right: 0;
    top: 831px;
    display: flex;
    align-items: center;
    gap: 10px;
  }
  .footer-rule {
    height: 1.5px;
    background: var(--red);
    flex: 1;
  }
  .footer-rule.left { flex: 0 0 135px; }
  .slogan {
    font-size: 10.5px;
    color: var(--ink);
    white-space: nowrap;
  }
</style>
</head>
<body>
  <main class="letterhead">
    <header class="brand">
      <span class="brand-mark"></span>
      <span class="brand-name">Brightfield<br>Ventures</span>
    </header>

    <address class="contact">
      <div class="address">448 Willowmere Ave<br>Ste 210 Maplecrest, CA 95999</div>
      <div class="contact-row">
        <svg viewBox="0 0 10 10" aria-hidden="true"><path d="M2.2 0.8 3.8 2.8 2.9 3.9C3.6 5.3 4.7 6.4 6.1 7.1L7.2 6.2 9.2 7.8 8.2 9.2C4.2 9 1 5.8 0.8 1.8Z" fill="var(--red)"/></svg>
        <span>916-555-0187</span>
      </div>
      <div class="contact-row">
        <svg viewBox="0 0 10 10" aria-hidden="true"><rect x="0.5" y="2" width="9" height="6.2" fill="var(--red)"/><path d="M0.8 2.3 5 5.6 9.2 2.3" stroke="#fff" stroke-width="0.9" fill="none"/></svg>
        <span>info@brightfieldventures.example</span>
      </div>
      <div class="contact-row">
        <svg viewBox="0 0 10 10" aria-hidden="true"><g fill="none" stroke="var(--red)" stroke-width="0.9"><circle cx="5" cy="5" r="4.2"/><ellipse cx="5" cy="5" rx="1.8" ry="4.2"/><path d="M0.8 5H9.2M1.5 3H8.5M1.5 7H8.5"/></g></svg>
        <span>www.brightfieldventures.example</span>
      </div>
    </address>

    <footer class="footer">
      <span class="footer-rule left"></span>
      <span class="slogan">Bringing building teams together to shape a stronger, steadier trade.</span>
      <span class="footer-rule"></span>
    </footer>
  </main>
</body>
</html>
```